lantern pathway for children needs a website designer

We need a website designer for our new extension to our company known as 'lantern pathway' providing shadow support services to children based in Singapore. We are a sister branch of a private clinic 'Bright horizons' providing speech language, occupational, and educational therapy to children.

We would like to use our own photos. So the selected design should have a frame with pictures to give us an idea but we will replace them with our own. We will be needing help with inputting information and changing information throughout.

We would like to see designs that are simple, and professional. We have a logo (see attached). The result should convey professionalism in shadow support, fostering independent thinking and moving students towards self-learning.

Target Market(s)

Teachers, psychologists, parents

Industry/Entity Type

Clinic

Requirements
Should not have
• too distracting colours

```html
<!DOCTYPE html>
<html lang="en">
<head>
<meta charset="utf-8">
<title>Lantern Pathway – Shadow Support</title>
<link href="https://fonts.googleapis.com/css2?family=Open+Sans:wght@300;400;600;700&display=swap" rel="stylesheet">
<style>
:root{
  --maroon:#8a0a0a;
  --maroon-dark:#5c0000;
  --page:#e6e6e6;
  --white:#ffffff;
  --text:#444444;
  --heading:#4a4a4a;
  --muted:#8a8a8a;
  --card:#e2e2e2;
  --footer:#232323;
  --footer-text:#9a9a9a;
  --footer-line:#3a3a3a;
}
*{margin:0;padding:0;box-sizing:border-box}
html,body{width:826px;height:1200px;overflow:hidden}
body{background:var(--page);font-family:'Open Sans',sans-serif;color:var(--text);position:relative}
.abs{position:absolute}
.login{left:696px;top:15px;font-size:9px;color:var(--muted);display:flex;align-items:center;gap:3px}
.sheet{left:90px;top:36px;width:647px;height:1046px;background:var(--white);box-shadow:0 0 3px rgba(0,0,0,.12)}
.brand{left:102px;top:56px;display:flex;align-items:center;gap:6px}
.brand-mark{width:14px;height:14px;border-radius:50%;background:var(--maroon)}
.brand-name{font-size:22px;font-weight:700;color:var(--maroon);letter-spacing:-.3px}
.contact{right:121px;top:52px;text-align:right}
.contact .label{font-size:9px;color:var(--muted)}
.contact .phone{font-size:13px;color:var(--maroon);line-height:14px}
.contact .email{font-size:9px;color:var(--muted);margin-top:4px}
.phone-icon{left:596px;top:53px}
.nav{left:82px;top:106px;width:663px;height:34px;background:var(--maroon)}
.nav-fold{top:140px}
.nav ul{list-style:none;position:absolute;left:215px;top:0;display:flex;height:34px}
.nav li{color:#fff;font-size:10px;line-height:34px;padding:0 6px;margin-right:2px;white-space:nowrap}
.nav li.active{background:var(--maroon-dark)}
.hero{left:90px;top:140px;width:647px;height:296px;background:linear-gradient(100deg,#d9d4cf 0%,#e6c9c6 30%,#c89478 55%,#2c4f78 78%,#9cc79a 100%)}
.arrow{width:21px;height:21px;border-radius:50%;background:rgba(40,40,40,.75);top:278px}
.hero-caption{left:147px;top:318px;font-size:14.5px;color:#fff;line-height:14px;text-shadow:0 1px 3px rgba(0,0,0,.7)}
.btn{left:149px;top:355px;width:125px;height:32px;background:var(--maroon);border:1px solid #fff;border-radius:3px;color:#fff;font-size:11.5px;font-weight:600;text-align:center;line-height:30px}
h2{font-weight:400;color:var(--heading);font-size:19px;text-align:center;position:absolute;left:90px;width:647px}
.about-text{left:124px;width:578px;top:497px;font-size:9.2px;line-height:14.2px;text-align:center}
.rule{left:157px;top:572px;width:512px;height:1px;background:#bdbdbd}
.sub{left:90px;width:647px;top:615px;text-align:center;font-size:9.2px}
.card{top:650px;width:169px;height:209px;background:var(--card);border:1px solid #d2d2d2;border-radius:3px;box-shadow:0 5px 5px -3px rgba(0,0,0,.35)}
.card .photo{height:120px;border-radius:3px 3px 0 0}
.card p{font-size:9.2px;line-height:14.2px;text-align:center;padding:0 11px;display:flex;align-items:center;justify-content:center;height:89px}
.list-item{left:150px;width:520px;display:flex;gap:11px;font-size:9.2px;line-height:14.2px}
.list-item svg{flex:none;margin-top:-1px}
.footer-band{left:0;top:1082px;width:826px;height:6px;background:var(--maroon)}
.footer{left:0;top:1088px;width:826px;height:112px;background:var(--footer)}
.fcol h4{font-size:11px;font-weight:400;color:var(--maroon);margin-bottom:2px}
.fcol li{list-style:none;font-size:9.2px;color:var(--footer-text);line-height:15.5px}
.vline{width:1px;background:var(--footer-line);top:1088px;height:112px}
.fcall{left:326px;top:1106px;font-size:9.2px;color:#bbb}
.fcall .num{color:var(--maroon);font-size:11px}
.femail{left:438px;top:1111px;font-size:9.2px;color:#bbb}
.social{top:1114px;width:21px;height:21px;border-radius:4px}
.hline{left:307px;top:1162px;width:427px;height:1px;background:var(--footer-line)}
.copy{right:90px;top:1173px;font-size:8.5px;color:#5a3a3a}
</style>
</head>
<body>
<div class="abs login">
  <svg width="8" height="10" viewBox="0 0 8 10"><rect x="0" y="4" width="8" height="6" fill="#222"/><path d="M2 4V2.5a2 2 0 0 1 4 0V4" stroke="#222" stroke-width="1.3" fill="none"/></svg>LOGIN
</div>

<div class="abs sheet"></div>

<div class="abs brand"><span class="brand-mark"></span><span class="brand-name">Lantern Pathway</span></div>

<svg class="abs phone-icon" width="12" height="18" viewBox="0 0 12 18"><rect x="1" y="1" width="10" height="16" rx="1.5" fill="none" stroke="#222" stroke-width="1.6"/><rect x="3" y="3" width="6" height="9" fill="#222"/></svg>
<div class="abs contact">
  <div class="label">call us for enquiries</div>
  <div class="phone">+65 6100 2480</div>
  <div class="email">enquiries@kestrelhill-clinic.sg</div>
</div>

<nav class="abs nav">
  <ul>
    <li class="active">HOME</li><li>ABOUT US</li><li>MISSION</li><li>OUR SERVICES</li><li>SHADOW SUPPORT</li><li>CONTACT US</li>
  </ul>
</nav>
<svg class="abs nav-fold" style="left:82px" width="8" height="8"><polygon points="0,0 8,0 8,8" fill="#3a0000"/></svg>
<svg class="abs nav-fold" style="left:737px" width="8" height="8"><polygon points="0,0 8,0 0,8" fill="#3a0000"/></svg>

<div class="abs hero" role="img" aria-label="Photo of a therapist playing with a young child using finger puppets"></div>
<div class="abs arrow" style="left:116px"><svg width="21" height="21"><path d="M12 6l-4 4.5 4 4.5" stroke="#ddd" fill="none" stroke-width="1.2"/></svg></div>
<div class="abs arrow" style="left:691px"><svg width="21" height="21"><path d="M9 6l4 4.5-4 4.5" stroke="#ddd" fill="none" stroke-width="1.2"/></svg></div>
<div class="abs hero-caption">Three month intensive training by our<br>Speech Language Pathologists</div>
<div class="abs btn">REGISTER NOW</div>

<h2 style="top:461px">About Us</h2>
<p class="abs about-text">Lantern Pathway is part of the Kestrel Hill Group of Companies, who are providing speech language therapy, occupational therapy and educational therapy services to both the Singapore and the international school community.<br>Lantern Pathway aims to work in an integrated manner, respecting the work of the respective professionals involved and collaborating effectively.</p>
<div class="abs rule"></div>

<h2 style="top:590px">Our Services</h2>
<p class="abs sub">We provide a full fledged, seamless service that serves to:</p>

<div class="abs card" style="left:142px">
  <div class="photo" role="img" aria-label="Photo of a therapist working with a boy at a small table" style="background:linear-gradient(90deg,#d8e3ea,#8fb4d6 45%,#e9ddc6)"></div>
  <p>Train shadows with a strong focus on equipping them with dynamic, clinical skills.</p>
</div>
<div class="abs card" style="left:329px">
  <div class="photo" role="img" aria-label="Photo of a therapist playing with a toddler using puppets" style="background:linear-gradient(100deg,#e2dcd6,#d9a9b5 35%,#c29078 60%,#2f5079 80%,#a7cfa1)"></div>
  <p>Provide families with well-trained Shadows who are mentored by Speech Language Pathologists and Professional Therapists to carry out shadow support.</p>
</div>
<div class="abs card" style="left:515px">
  <div class="photo" role="img" aria-label="Photo of a teacher with students in a classroom" style="background:linear-gradient(90deg,#b9a98a,#4c5563 40%,#c9c3bb 70%,#d9a7b2)"></div>
  <p>Provide families with well-trained Shadows who are mentored by Speech Language Pathologists and Professional Therapists to carry out shadow support.</p>
</div>

<h2 style="top:898px">How You Can Collaborate With Us</h2>
<div class="abs list-item" style="top:947px">
  <svg width="20" height="20" viewBox="0 0 20 20"><circle cx="10" cy="10" r="10" fill="var(--maroon)"/><path d="M5.5 10.5l3 3 6-6.5" stroke="#fff" stroke-width="2.2" fill="none"/></svg>
  <span>Shadow Support will participate in a collaborative working relationship with the professionals working with each student to facilitate progress</span>
</div>
<div class="abs list-item" style="top:989px">
  <svg width="20" height="20" viewBox="0 0 20 20"><circle cx="10" cy="10" r="10" fill="var(--maroon)"/><path d="M5.5 10.5l3 3 6-6.5" stroke="#fff" stroke-width="2.2" fill="none"/></svg>
  <span>Goals set out by professionals will be supported by the Shadow Support</span>
</div>
<div class="abs list-item" style="top:1017px">
  <svg width="20" height="20" viewBox="0 0 20 20"><circle cx="10" cy="10" r="10" fill="var(--maroon)"/><path d="M5.5 10.5l3 3 6-6.5" stroke="#fff" stroke-width="2.2" fill="none"/></svg>
  <span>Frequent feedback and updates will be provided by the Shadow Support so that goals can remain relevant and up to date</span>
</div>

<div class="abs footer-band"></div>
<footer class="abs footer"></footer>
<div class="abs vline" style="left:198px"></div>
<div class="abs vline" style="left:306px"></div>
<div class="abs fcol" style="left:105px;top:1102px">
  <h4>Quick links</h4>
  <ul><li>For Parents</li><li>Registration Form</li><li>Cost Estimation</li><li>For Schools</li></ul>
</div>
<div class="abs fcol" style="left:224px;top:1102px">
  <h4>Menu</h4>
  <ul><li>About us</li><li>Mission</li><li>Our services</li><li>Contact</li></ul>
</div>
<div class="abs fcall">call us for enquiries<div class="num">+65 6100 2480</div></div>
<div class="abs femail">enquiries@kestrelhill-clinic.sg</div>
<div class="abs social" style="left:663px;background:#2a9fd8;border-radius:50%"></div>
<div class="abs social" style="left:689px;background:#3b5a9a"></div>
<div class="abs social" style="left:715px;background:#35a8e0"></div>
<div class="abs hline"></div>
<div class="abs copy">Copyright © 2014 lantern pathway, All Rights Reserved</div>
</body>
</html>
```